Word Template Designs for Offensive Security Professional Services Report

We need a Microsoft Word Template designed for our Offensive Security professional services reports which includes the following services:

RedTeaming
Network Penetration Testing
Web Application Penetration Testing
Wireless Penetration Testing
Social Engineering

The templates should include the following:
Cover Page design with our Logo included
Executive Summary Page design
Detailed Findings Page design
Design for Last Page

Lastly, I would also like a template I can use for all of my Statements of Work

Requirements
Must have
• Beautiful Eye Catching HD pictures that represent my Offensive Security projects
The design should flow well with our logo

```html
<!DOCTYPE html>
<html lang="en">
<head>
<meta charset="utf-8">
<title>Vantage Breach – Scope of Work Template</title>
<link href="https://fonts.googleapis.com/css2?family=Roboto:wght@400;500;700&family=Lato:wght@400;700&display=swap" rel="stylesheet">
<style>
  :root{
    --stage:#7b7b7b;
    --paper:#ffffff;
    --green:#5a8f3a;
    --green-light:#8fc06a;
    --ink:#1e1e1e;
    --ink-soft:#3a3a3a;
    --row-shade:#e3e3e3;
    --black:#000000;
  }
  *{margin:0;padding:0;box-sizing:border-box}
  html,body{width:676px;height:1200px;overflow:hidden;background:var(--stage)}
  body{position:relative;font-family:"Lato",Arial,sans-serif;color:var(--ink)}
  .page{position:absolute;width:235px;height:333px;background:var(--paper);overflow:hidden;box-shadow:0 2px 6px rgba(0,0,0,.25)}
  .abs{position:absolute}
  .heading{font-family:"Roboto",Arial,sans-serif}

  /* Cover */
  .cover{left:221px;top:60px}
  .brand{display:flex;flex-direction:column;align-items:center}
  .brand-mark{width:27px;height:27px;border-radius:50%;background:#2b2b2b;border:1px solid #bdbdbd}
  .brand-name{font-family:"Roboto",Arial,sans-serif;font-weight:700;font-size:8px;color:var(--green);margin-top:2px;white-space:nowrap}
  .cover .brand{left:8px;top:16px;width:80px}
  .cover-art{right:0;top:108px;width:150px;height:197px;
    background:radial-gradient(ellipse at 70% 60%,#7fae8a 0%,#a9c7ae 30%,#dfe9e0 60%,rgba(255,255,255,0) 85%)}
  .cover-kicker{left:19px;top:72px;font-size:8.5px;font-weight:700;color:var(--green)}
  .cover-title{left:19px;top:83px;font-size:10px;font-weight:700;color:var(--ink-soft);line-height:12px}
  .cover-for{left:20px;top:128px;font-size:7px;font-weight:700;line-height:9.5px}
  .cover-by{left:19px;top:220px;font-size:7px;font-weight:700}
  .cover-details{left:19px;top:229px;font-family:"Roboto",Arial,sans-serif;font-size:4.6px;line-height:5.7px;color:var(--ink-soft)}
  .cover-details p+p{margin-top:5.5px}
  .cover-footer{left:0;bottom:0;width:100%;height:28px;background:var(--green);border-top:2px solid #fff;
    display:flex;align-items:center;justify-content:space-around;font-size:4.2px;color:#fff;font-family:"Roboto",Arial,sans-serif}
  .cover-footer span{display:flex;align-items:center;gap:2px}

  /* Revision page */
  .revision{left:103px;top:417px}
  .revision h2{position:absolute;top:14px;width:100%;text-align:center;font-size:9.5px;color:var(--green);font-weight:700}
  .rev-table{position:absolute;top:31px;left:0;width:100%;font-family:"Roboto",Arial,sans-serif}
  .rev-head{display:grid;grid-template-columns:68px 83px 1fr;background:var(--black);color:#fff;font-size:6.8px;height:13px;align-items:center;padding-left:15px}
  .rev-row{display:grid;grid-template-columns:68px 83px 1fr;font-size:3.8px;padding-left:16px;margin-top:3px}
  .page-tag{position:absolute;left:0;background:var(--black);color:#fff;font-size:3.8px;display:flex;align-items:center;justify-content:center;width:25px;height:10px}

  /* Table of contents */
  .toc{left:378px;top:417px}
  .toc .brand{left:0;top:10px;width:100%}
  .toc-band{position:absolute;left:0;top:64px;width:100%;height:17px;background:var(--green);color:#fff;text-align:center;font-size:11.5px;font-weight:700;line-height:17px}
  .toc-list{position:absolute;top:97px;left:0;width:100%;list-style:none;font-family:"Roboto",Arial,sans-serif}
  .toc-list li{display:flex;justify-content:space-between;height:11.9px;align-items:center;padding:0 10px 0 9px;font-size:4.2px}
  .toc-list li.major{background:var(--row-shade);font-weight:700}

  /* Body pages */
  .content{padding-top:11px}
  .band-title{background:var(--green);color:#fff;text-align:center;font-size:10px;font-weight:700;height:15px;line-height:15px;margin-top:2px}
  .tab{display:inline-block;background:var(--green);color:#fff;font-family:"Roboto",Arial,sans-serif;font-weight:700;font-size:5.6px;padding:1.5px 4px 1.5px 9px;margin-top:6px}
  .copy{font-size:3.6px;line-height:4.6px;padding:2px 9px 0 9px;color:var(--ink-soft)}
  .copy p+p{margin-top:3px}
  .accent{color:var(--green)}
  .services{display:grid;grid-template-columns:1fr 1fr;padding:2px 12px;font-size:3.7px;row-gap:3px}
  .services span::before{content:"✓ ";color:var(--green)}
  .bullets{display:grid;grid-template-columns:1fr 1fr;padding:3px 14px 2px 26px;font-size:3.7px;row-gap:4.3px}
  .bullets span{position:relative}
  .bullets span::before{content:"";position:absolute;left:-6px;top:1px;width:3px;height:3px;border-radius:50%;background:var(--green)}
  .deliv{list-style:none;padding:2px 9px 0 14px;font-size:3.7px;line-height:4.6px}
  .deliv li{position:relative;margin-bottom:3.2px}
  .deliv li::before{content:"";position:absolute;left:-4px;top:1.6px;width:1.6px;height:1.6px;border-radius:50%;background:var(--green)}
  .site{position:absolute;right:9px;bottom:11px;font-size:3.8px;color:var(--green)}
  .summary{left:378px;top:770px}
  .phases{left:103px;top:770px}
  .phases .content{padding-top:11px}
  .phases .tab{margin-top:0}
  .phases .tab.next{margin-top:5px}
</style>
</head>
<body>

<!-- Cover -->
<section class="page cover">
  <div class="abs cover-art" role="img" aria-label="Glowing green circuit board with shield and padlock"></div>
  <div class="abs brand"><div class="brand-mark"></div><div class="brand-name">Vantage Breach</div></div>
  <p class="abs heading cover-kicker">SCOPE OF WORK :</p>
  <h1 class="abs heading cover-title">External, Internal Network,<br>Wireless and Web Application Penetration<br>Testing Engagement</h1>
  <p class="abs heading cover-for">PREPARED FOR :<br>[Client Name]</p>
  <p class="abs heading cover-by">PREPARED BY :</p>
  <div class="abs cover-details">
    <p>Daniel Hargrove, CISSP, OSCE, OSCP<br>[Company Name], LLC</p>
    <p>4820 Ridgeline Ave Suite 210<br>Austin Texas 78701<br>www.vantage-breach.com</p>
    <p>Daniel.Hargrove@Vantage-Breach.com<br>Office 1800.555.0142<br>Mobile: 512.555.0187<br>August 2, 2018</p>
  </div>
  <footer class="abs cover-footer">
    <span><svg width="5" height="5" viewBox="0 0 10 10"><circle cx="5" cy="5" r="4.3" fill="none" stroke="#fff"/><path d="M3.5 3c0 2 1.5 3.5 3.5 3.5" stroke="#fff" fill="none"/></svg>1-800-555-0142</span>
    <span><svg width="5" height="4" viewBox="0 0 10 8"><rect x=".5" y=".5" width="9" height="7" fill="none" stroke="#fff"/><path d="M.5 .5L5 4.5 9.5 .5" stroke="#fff" fill="none"/></svg>info@example.com</span>
    <span><svg width="5" height="5" viewBox="0 0 10 10"><circle cx="5" cy="5" r="4.3" fill="none" stroke="#fff"/><path d="M.7 5h8.6M5 .7v8.6" stroke="#fff"/></svg>www.vantage-breach.com</span>
  </footer>
</section>

<!-- Revision control -->
<section class="page revision">
  <h2 class="heading">DOCUMENT REVISION CONTROL</h2>
  <div class="rev-table">
    <div class="rev-head"><span>Revision Number</span><span>Revision</span><span>Revision Date</span></div>
    <div class="rev-row"><span>1.0</span><span>Initial</span><span>8/2/18</span></div>
  </div>
  <div class="page-tag" style="top:319px">Page 2</div>
</section>

<!-- Table of contents -->
<section class="page toc">
  <div class="abs brand"><div class="brand-mark"></div><div class="brand-name">Vantage Breach</div></div>
  <h2 class="toc-band heading">TABLE OF CONTENTS</h2>
  <ul class="toc-list">
    <li><span>TABLE OF CONTENTS</span><span>3</span></li>
    <li class="major"><span>PROPOSAL SUMMARY</span><span>4</span></li>
    <li><span>ENGAGEMENT OVERVIEW</span><span>4</span></li>
    <li><span>Phase One: External Network Penetration Testing</span><span>4</span></li>
    <li><span>Phase Two: Internal Network Penetration Testing</span><span>4</span></li>
    <li><span>Phase Three: Wireless Penetration Testing</span><span>5</span></li>
    <li><span>Phase Four: Targeted Web Application Penetration Testing</span><span>5</span></li>
    <li><span>ENGAGEMENT DELIVERABLES</span><span>6</span></li>
    <li><span>PHASE SPECIFIC TASKS</span><span>7</span></li>
    <li><span>Phase One: External Network Penetration Testing</span><span>7</span></li>
    <li><span>Phase Two: Internal Network Penetration Testing</span><span>9</span></li>
    <li><span>Phase Three: Wireless Penetration Testing</span><span>11</span></li>
    <li><span>Phase Four: Targeted Web Application Penetration Testing</span><span>12</span></li>
    <li class="major"><span>ABOUT [COMPANY NAME]</span><span>15</span></li>
    <li><span>CONSULTANT PROFILE</span><span>15</span></li>
    <li class="major"><span>SCOPE APPROVAL</span><span>16</span></li>
    <li><span>CLIENT ACTIVITY CHECKLIST</span><span>16</span></li>
    <li><span>ACKNOWLEDGEMENTS</span><span>16</span></li>
  </ul>
  <div class="page-tag" style="top:315px">Page 3</div>
</section>

<!-- Phases three & four -->
<section class="page phases">
  <div class="content">
    <h3 class="tab">PHASE THREE:WIRELESS PENETRATION TESTING</h3>
    <div class="copy">
      <p>[Company Name] will assess [Client Name] guest and production wireless networks. During testing, [Company Name] will attempt to gain access to hosts belonging to [Client Name]' internal network presence and wireless controllers. [Company Name] will exploit vulnerabilities identified during the vulnerability identification process. After a system or information is compromised, [Company Name] will gather appropriate evidence for proof of information or system compromise.</p>
      <p>[Company Name] will conduct this work on-site while performing the assessment in collaboration with [Client Name]. After the assessment is complete, [Company Name] will develop a formal report that will include the items described in the Final Report Summary.</p>
    </div>
    <h3 class="tab next">PHASE FOUR: TARGETED WEB APPLICATION PENETRATION TESTING</h3>
    <div class="copy">
      <p>[Company Name] will conduct a Targeted Web Application Penetration Testing assessment of the target web application and supporting services as an unauthorized/unauthenticated and authorized/authenticated users' perspective to determine the exposed vulnerabilities that are accessible to an attacker.</p>
      <p><span class="accent">Unauthorized/Unauthenticated</span> – An Unauthenticated Assessment of your web application gives a realistic view of what an attacker with a simple Internet connection and no privileges would be able to access, find, and possibly exploit. This type of assessment tests the strengths of your application's authentication mechanism(s) and any other vulnerability associated with the application.</p>
      <p><span class="accent">Authorized/Authenticated</span> – An authenticated Assessment of your web application gives a realistic view of what an attacker with basic and administrative privileges would be able to access, find, and possibly exploit. This type of assessment tests the strengths of your applications to withstand attacks by authorized users who have valid credentials to authenticate to the application.</p>
      <p>Additional testing may include the following :</p>
    </div>
    <div class="bullets">
      <span>Information Leakage</span><span>OS Command Injection</span>
      <span>Session Management</span><span>Local and Remote File Inclusion</span>
      <span>Default Configurations</span><span>Cross Site Request Forgery</span>
      <span>Authentication abuse</span><span>Application and Business Logic Flaws</span>
      <span>Client-Side Cache</span><span>Proper Input Validation</span>
      <span>Authorization exploitation</span><span>Privilege Escalation Opportunities</span>
      <span>SQL Injection, (backend database enumeration and manipulation)</span><span>Client-Side Code<br><br>Server-Side Input Validation</span>
    </div>
    <div class="copy"><p>[Company Name] follows a well-developed and proven methodology to assess the security of web-based applications as defined in the specific tasks in the next section. After the assessment is complete, [Company Name] will develop a formal report that will include the items described in the Final Report Summary.</p></div>
    <h3 class="tab next">ENGAGEMENT DELIVERABLES</h3>
    <div class="copy"><p>[Company Name] will provide the following Deliverables to [Client Name]:</p></div>
    <ul class="deliv">
      <li>Weekly Status Updates if applicable</li>
      <li>Final Report and Presentation delivered at the end of the engagement</li>
      <li>Onsite Q&amp;A session with our consultants to discuss the process, findings, and recommendations, and answer questions related to the engagement.</li>
    </ul>
  </div>
  <div class="page-tag" style="top:318px">Page 5</div>
  <span class="site">www.vantage-breach.com</span>
</section>

<!-- Proposal summary -->
<section class="page summary">
  <div class="content" style="padding-top:11px">
    <h2 class="band-title heading">PROPOSAL SUMMARY</h2>
    <div class="copy" style="padding-top:5px"><p>[Company Name] is proud to present this multi-phase Scope of Work to [Client Name] to meet their Penetration Testing Requirements. [Company Name] LLC's security consultants have expert knowledge in Network Security and Web Applications, Security Controls, process and procedures, best practices, vulnerabilities and countermeasures. Our security consultants will perform the penetration testing presented in this Scope of Work.</p></div>
    <h3 class="tab" style="margin-top:8px">ENGAGEMENT OVERVIEW</h3>
    <div class="copy">
      <p>Based on the information provided, [Company Name] understands that [Client Name] objectives are to have [Company Name] LLC provide penetration testing, ethical hacking and risk management services to [Client Name] to help ensure that the systems are working in a safe secure manner in every respect and by ensuring the proper preservation of all data's Confidentiality, Integrity, and Availability (CIA).</p>
      <p>From [Company Name]'s understanding, [Client Name] has requested that the penetration testing be performed from a grey box perspective to determine the exposed vulnerabilities of the networks, applications and wireless implementations.</p>
      <p class="accent">In response to these requirements, [Company Name] will perform the following services :</p>
    </div>
    <div class="services">
      <span>External Network Penetration Testing</span><span>Internal Network Penetration Testing</span>
      <span>Wireless Network Penetration Testing</span><span>Targeted Web Application Penetration Testing</span>
    </div>
    <h3 class="tab" style="margin-top:5px">PHASE ONE: EXTERNAL NETWORK PENETRATION TESTING</h3>
    <div class="copy">
      <p>[Company Name] will conduct a Network Penetration Testing assessment of the external network, aka the Internet presence to help identify existing vulnerabilities and their associated risks. [Company Name] will discover and identify hosts belonging to [Client Name] external network, identify vulnerabilities and exploit vulnerabilities identified during the ethical hacking process. After a system is compromised, the vulnerabilities and any applicable exploits will be documented in a detailed, repeatable process.</p>
      <p>[Company Name] will conduct this work remotely while performing the Network Penetration Testing assessment in collaboration with [Client Name] personnel. After the assessment is complete, [Company Name] will develop a formal report that will include the items described in the Final Report Summary.</p>
    </div>
    <h3 class="tab" style="margin-top:5px">PHASE TWO: INTERNAL NETWORK PENETRATION TESTING</h3>
    <div class="copy">
      <p>[Company Name] will conduct a penetration test of the [Client Name] internal network, aka their private LAN. [Company Name] will exploit vulnerabilities identified during the vulnerability identification process. After a system is compromised, the vulnerabilities and any applicable exploits will be documented in a detailed, repeatable process.</p>
      <p>[Company Name] will conduct this work onsite initially and remotely after deploying [Company Name]'s internal network attack server. The Network Penetration Testing will be conducted in collaboration with [Client Name] personnel. After the assessment is complete, [Company Name] will develop a formal report that will include the items described in the Final Report Summary.</p>
      <p><b>Note :</b> The attack server's purpose is to facilitate internal network penetration testing efforts from a remote offsite location. This will help emulate an attacker who has gained access to the internal network and is outside of the organization. No Denial of Service or testing outside of the internal network penetration testing efforts will be conducted via the attack server.</p>
    </div>
  </div>
  <div class="page-tag" style="top:318px">Page 4</div>
  <span class="site">www.vantage-breach.com</span>
</section>

</body>
</html>
```